Business cards and stationary design

We just completed the design of our new logo and we need to print new business cards and letterhead for our nonprofit. We are looking for a fresh new design that shows off our new logo. On letterhead, we must have a column on the right or left to include our Board of Directors (up to 45 names) (see attachment)

Industry/Entity Type

Non-Profit

Contact Information for Business Card

Standard business card with name, title, Company name, mailing address phone numbers, email address and website. Tagline on back "Opening doors for every family"

Font styles to use
Sans Serif

Requirements
Must have
• include pertinent information above
• new logo
• fonts compatible with logo
• should use logo colors only
Nice to have
• tag lines

```html
<!DOCTYPE html>
<html lang="en">
<head>
<meta charset="utf-8">
<title>Shelter Bridge Center – Business Card</title>
<link rel="stylesheet" href="https://fonts.googleapis.com/css2?family=Roboto:wght@400;500;700&display=swap">
<style>
  :root {
    --teal: #0683a6;
    --red: #d6202b;
    --ink-grey: #555555;
    --card-white: #f8f8f8;
    --backdrop: #e2e2e2;
    --on-band: #ffffff;
  }
  * { margin: 0; padding: 0; box-sizing: border-box; }
  html, body {
    width: 1200px; height: 582px; overflow: hidden;
    background: var(--backdrop);
    font-family: "Roboto", Arial, sans-serif;
  }
  .stage { position: relative; width: 1200px; height: 582px; }
  .card {
    position: absolute; top: 158px;
    width: 464px; height: 264px;
    background: var(--card-white);
    overflow: hidden;
  }
  .card--front { left: 122px; }
  .card--back { left: 602px; }

  .holder { position: absolute; left: 30px; top: 68px; }
  .holder__name {
    color: var(--teal); font-weight: 500; font-size: 22px; line-height: 26px; letter-spacing: 0.2px;
  }
  .holder__title {
    color: var(--red); font-weight: 500; font-size: 14px; line-height: 16px;
  }
  .front__mark {
    position: absolute; right: 33px; top: 146px;
    color: var(--teal); font-weight: 700; font-size: 11px; letter-spacing: 0.6px;
  }
  .info-band {
    position: absolute; left: 0; right: 0; top: 166px; bottom: 0;
    background: var(--teal); color: var(--on-band);
  }
  .contact-list {
    position: absolute; left: 30px; top: 28px; list-style: none;
    font-size: 10.5px; font-weight: 500;
  }
  .contact-list li { display: flex; align-items: center; height: 15px; }
  .contact-list svg { width: 10px; height: 10px; margin-right: 7px; fill: var(--on-band); }
  .address {
    position: absolute; right: 33px; top: 28px; text-align: right;
    font-size: 10.5px; font-weight: 500; font-style: normal; line-height: 15px;
  }
  .address__org { font-weight: 700; }

  .back__name {
    position: absolute; left: 0; right: 0; top: 143px; text-align: center;
    color: var(--teal); font-weight: 500; font-size: 21px; letter-spacing: 2.5px;
  }
  .back__tagline {
    position: absolute; left: 0; right: 0; top: 222px; text-align: center;
    color: var(--ink-grey); font-weight: 500; font-size: 11.5px; letter-spacing: 0.4px;
  }
</style>
</head>
<body>
<main class="stage">
  <section class="card card--front">
    <div class="holder">
      <div class="holder__name">DANIEL REYES</div>
      <div class="holder__title">CEO/FOUNDER</div>
    </div>
    <div class="front__mark">SHELTER BRIDGE</div>
    <div class="info-band">
      <ul class="contact-list">
        <li><svg viewBox="0 0 10 10"><path d="M2 0.5 L3.6 0.5 L4.3 2.8 L3.2 3.8 Q4.2 5.8 6.2 6.8 L7.2 5.7 L9.5 6.4 L9.5 8 Q9.5 9.5 8 9.5 Q4.5 9.3 2.4 7.6 Q0.6 5.5 0.5 2 Q0.5 0.5 2 0.5Z"/></svg>555 210 4836</li>
        <li><svg viewBox="0 0 10 10"><path d="M0.5 2 H9.5 V8.5 H0.5Z M1.2 2.4 L5 5.4 L8.8 2.4" fill="none" stroke="#fff" stroke-width="1"/></svg>dan@shelterbridge.org</li>
        <li><svg viewBox="0 0 10 10"><circle cx="5" cy="5" r="4.5"/><path d="M3 3.2 L5 4 L4.4 6 L6.5 7.8 L6.2 5.2 L7.6 4" fill="none" stroke="#0683a6" stroke-width="0.9"/></svg>www.shelterbridge.org</li>
      </ul>
      <address class="address">
        <div class="address__org">SHELTER BRIDGE CENTER</div>
        <div>4218 Juniper Lane</div>
        <div>Fairview, Alaska 39182</div>
      </address>
    </div>
  </section>

  <section class="card card--back">
    <div class="back__name">SHELTER BRIDGE CENTER</div>
    <p class="back__tagline">Opening doors for every family</p>
  </section>
</main>
</body>
</html>
```